WordPress website design for wealth management company

A modern clean look website for a service company. This is mostly for information only, with a form to capture prospect contact information and schedule a 15 minutes call. There will be several static pages describe what services we offer, how we are different, and a blog section for posting articles and share resources. A section for client testimonials.
I want a website that is easy to understand and maintain. No proprietary plugins that cost extra. The main thing I need help is the visual layout / color palette that present a clean and professional look, select the suitable stock photos that convey the image of trust, professional, innovative, and high service.
Some websites with style I like include the following
- https://www.halvorbrook.com/
- https://www.trivanplanningworks.com/
- https://morvellfunds.com/private-equity-partners/
Also some websites in other industries with clean modern look
- https://zentrell.com/
- https://quovra.com/
- https://www.plumtorvik.com/
I want the end product to be a fully functional website that I can upload into web hosting service I use and I can easily add content and maintain myself in the future.

```html
<!DOCTYPE html>
<html lang="en">
<head>
<meta charset="utf-8">
<title>Marrowind Wealth</title>
<link href="https://fonts.googleapis.com/css2?family=Plus+Jakarta+Sans:wght@400;500;600;700;800&display=swap" rel="stylesheet">
<style>
:root{
  --purple:#4e1d7a;
  --purple-deep:#3a1160;
  --purple-mid:#7a3fa6;
  --yellow:#fbb829;
  --lilac:#ede6f0;
  --cream:#fde9b6;
  --ink:#1d1d1f;
  --text:#3a3a3f;
  --field:#eef0f4;
  --black:#050505;
}
*{box-sizing:border-box;margin:0;padding:0}
html,body{width:1200px;height:4188px;overflow:hidden}
body{font-family:"Plus Jakarta Sans",sans-serif;color:var(--text);background:#fff;position:relative}
.abs{position:absolute}
.topbar{left:0;top:0;width:1200px;height:54px;background:var(--yellow);display:flex;align-items:center;justify-content:center;gap:34px;font-size:14px;font-weight:700;color:var(--ink)}
.header{left:0;top:54px;width:1200px;height:104px}
.brand{display:flex;align-items:center;gap:10px}
.brand-dot{width:14px;height:14px;border-radius:50%;background:var(--yellow);flex:none}
.brand-name{font-weight:800;color:var(--purple);letter-spacing:2px;font-size:19px;line-height:22px;white-space:nowrap}
.nav{display:flex;gap:36px;font-size:15px;font-weight:700;color:var(--ink)}
.search{left:1039px;top:83px;width:48px;height:48px;border-radius:50%;background:var(--purple);display:flex;align-items:center;justify-content:center}
.hero-photo{left:0;top:158px;width:1200px;height:557px;background:linear-gradient(90deg,#d9dde3 0%,#c7ccd6 30%,#b6a7c7 50%,#7e49a6 62%,var(--purple) 100%)}
.hero-text{left:716px;top:290px;width:440px;color:#fff}
.hero-text .eyebrow{font-size:22px;font-weight:800}
.hero-text h1{font-size:36px;font-weight:800;margin-top:22px;white-space:nowrap}
.hero-text p{font-size:15px;line-height:28px;margin-top:26px;width:400px}
.btn{display:inline-flex;align-items:center;justify-content:center;background:var(--yellow);color:var(--purple-deep);font-weight:700;border-radius:8px}
.hero-btn{margin-top:28px;width:167px;height:49px;font-size:17px}
.section-title{left:0;width:1200px;text-align:center;font-size:31px;font-weight:800;color:var(--purple)}
.about-copy{left:110px;top:932px;width:490px;text-align:center;font-size:15.5px;line-height:34.5px;color:var(--ink)}
.about-btn{left:434px;top:1192px;width:166px;height:49px;font-size:17px}
.about-name{left:664px;top:1040px;width:330px;display:flex;align-items:center;justify-content:center;gap:14px}
.about-name .brand-dot{width:22px;height:22px}
.about-name .brand-name{font-size:28px;line-height:34px}
.services{left:0;top:1337px;width:1200px;height:631px;background:var(--lilac);border-radius:80px}
.svc{width:240px;font-size:15.5px;line-height:26px;color:var(--ink)}
.svc h3{font-size:20px;font-weight:800;color:var(--purple);margin-bottom:14px}
.svc .icon{height:56px;margin-bottom:14px}
.svc.left{text-align:right}
.svc.left .icon{display:flex;justify-content:flex-end}
.svc-photo{left:393px;width:407px;height:429px}
.card{width:314px}
.card-img{width:314px;height:246px;border-radius:10px;position:relative}
.date{position:absolute;left:0;top:0;background:#fff;padding:9px 14px;border-radius:10px 0 10px 0;font-size:13px;font-weight:800;color:var(--purple)}
.card h4{font-size:16.5px;font-weight:800;color:var(--purple);margin-top:40px}
.card p{font-size:17px;line-height:38px;color:var(--ink);margin-top:10px}
.card a{display:block;margin-top:2px;font-size:17px;font-weight:800;color:var(--purple);text-decoration:underline}
.arrow{width:48px;height:48px;border-radius:50%;background:var(--purple);display:flex;align-items:center;justify-content:center}
.testimonials{left:0;top:2663px;width:1200px;height:581px;background:var(--cream);border-radius:70px}
.quote{left:265px;top:2848px;width:664px;font-size:15.5px;line-height:33px;color:var(--ink);text-align:justify}
.avatar{left:450px;top:3007px;width:104px;height:104px;border-radius:50%;background:linear-gradient(180deg,#7cc4e8,#3d9dd2)}
.dots{left:568px;top:3159px;display:flex;gap:16px}
.dots span{width:9px;height:9px;border-radius:50%;background:var(--purple)}
.map{left:110px;top:3341px;width:438px;height:342px;border-radius:16px;background:linear-gradient(135deg,#5c6b85,#8390a4 55%,#6f7b8f)}
.field{background:var(--field);border:1px solid #d5d9e0;display:flex;align-items:center;justify-content:space-between;padding:0 16px;font-size:11px;font-weight:700;color:var(--ink)}
.footer{left:0;top:3780px;width:1200px;height:408px;background:var(--black)}
.footer-nav{display:flex;gap:36px;font-size:15.5px;font-weight:700;color:#fff}
.social{display:flex;gap:9px}
.social span{width:35px;height:35px;border-radius:7px;background:#1565e0}
</style>
</head>
<body>

<div class="abs topbar">
  <span>SCHEDULE A 15 MINUTES CALL</span>
  <svg width="18" height="18" viewBox="0 0 24 24" fill="none" stroke="#1d1d1f" stroke-width="2"><path d="M5 3h4l2 5-3 2a12 12 0 0 0 6 6l2-3 5 2v4a2 2 0 0 1-2 2A18 18 0 0 1 3 5a2 2 0 0 1 2-2z"/></svg>
  <span>+1 999 999 9999</span>
</div>

<header class="abs header">
  <div class="abs brand" style="left:70px;top:40px">
    <span class="brand-dot"></span>
    <span class="brand-name">MARROWIND</span>
  </div>
  <nav class="abs nav" style="left:322px;top:42px">
    <span>HOME</span><span>ABOUT US</span><span>OUR SERVICES</span><span>TESTIMONIALS</span><span>CONTACT US</span>
  </nav>
</header>
<div class="abs search">
  <svg width="24" height="24" viewBox="0 0 24 24" fill="none" stroke="#fff" stroke-width="2.2"><circle cx="10.5" cy="10.5" r="6.5"/><path d="M15.5 15.5 21 21"/></svg>
</div>

<section>
  <div class="abs hero-photo" role="img" aria-label="Doctor and nurse reviewing a clipboard in a bright clinic corridor"></div>
  <div class="abs hero-text">
    <div class="eyebrow">WELCOME TO</div>
    <h1>MARROWIND WEALTH</h1>
    <p>Sed ut perspiciatis unde omnis iste natus error sit voluptatem accusantium doloremque laudantium, totam rem aperiam, eaque ipsa quae ab illo</p>
    <span class="btn hero-btn">GET STARTED</span>
  </div>
</section>

<section>
  <h2 class="abs section-title" style="top:854px">ABOUT US</h2>
  <p class="abs about-copy">Nemo enim ipsam voluptatem quia voluptas sit aspernatur aut odit aut fugit, sed quia consequuntur magni dolores eos qui ratione voluptatem sequi nesciunt. Neque porro quisquam est, qui dolorem ipsum quia dolor sit amet, consectetur, adipisci velit, sed quia non numquam eius modi tempora incidunt ut labore et dolore magnam aliquam quaerat voluptatem. Ut enim ad minima veniam, quis nostrum exercitationem ullam corporis suscipit</p>
  <span class="abs btn about-btn">LEARN MORE</span>
  <div class="abs brand about-name">
    <span class="brand-dot"></span>
    <span class="brand-name">MARROWIND WEALTH</span>
  </div>
</section>

<section class="abs services">
  <h2 class="abs section-title" style="top:50px">OUR SERVICES</h2>
  <div class="abs svc-photo" style="top:120px" role="img" aria-label="Smiling senior businesswoman portrait in a diamond frame">
    <svg width="407" height="429" viewBox="0 0 407 429">
      <polygon points="203,40 400,220 203,410 8,220" fill="#c9c4cc"/>
      <g fill="none" stroke="#4e1d7a" stroke-width="1.4" stroke-dasharray="4 4">
        <path d="M8 32H394M8 396H394M8 32V396M394 32V396"/>
      </g>
      <g fill="#ede6f0" stroke="#4e1d7a" stroke-width="1.6">
        <circle cx="6" cy="32" r="5"/><circle cx="400" cy="32" r="5"/><circle cx="6" cy="396" r="5"/><circle cx="400" cy="396" r="5"/>
      </g>
    </svg>
  </div>

  <div class="abs svc left" style="left:119px;top:140px">
    <h3>ORGANIZE</h3>
    <div class="icon"><svg width="56" height="50" viewBox="0 0 56 50" fill="none" stroke="#4e1d7a" stroke-width="2"><path d="M4 34 28 44 52 34 28 24z" fill="#fbb829"/><path d="M4 24 28 34 52 24 28 14z"/><path d="M4 14 28 24 52 14 28 4z"/></svg></div>
    <p>Nemo enim ipsam voluptatem quia voluptas sit aspernatur aut odit aut fugit, sed quia</p>
  </div>
  <div class="abs svc left" style="left:119px;top:396px">
    <div class="icon"><svg width="56" height="56" viewBox="0 0 56 56" fill="none" stroke="#4e1d7a" stroke-width="2"><circle cx="28" cy="28" r="23"/><circle cx="28" cy="28" r="14" fill="#fbb829"/><path d="m21 28 5 5 9-10"/></svg></div>
    <h3>EXECUTE</h3>
    <p>Nemo enim ipsam voluptatem quia voluptas sit aspernatur aut odit aut fugit, sed quia</p>
  </div>
  <div class="abs svc" style="left:836px;top:140px">
    <h3>VISUALIZE</h3>
    <div class="icon"><svg width="56" height="50" viewBox="0 0 56 50" fill="none" stroke="#4e1d7a" stroke-width="2"><rect x="4" y="4" width="44" height="30" rx="2"/><rect x="10" y="10" width="32" height="18" fill="#fbb829"/><circle cx="26" cy="19" r="5"/><path d="M20 44h12M26 34v10"/></svg></div>
    <p>Nemo enim ipsam voluptatem quia voluptas sit aspernatur aut odit aut fugit, sed quia</p>
  </div>
  <div class="abs svc" style="left:836px;top:396px">
    <div class="icon"><svg width="56" height="56" viewBox="0 0 56 56" fill="none" stroke="#4e1d7a" stroke-width="2"><rect x="4" y="6" width="40" height="32"/><path d="M12 32V24M20 32V18M28 32V22"/><circle cx="40" cy="34" r="8" fill="#fbb829"/><path d="m46 40 6 6"/></svg></div>
    <h3>STRATEGIZE</h3>
    <p>Nemo enim ipsam voluptatem quia voluptas sit aspernatur aut odit aut fugit, sed quia</p>
  </div>
</section>

<section>
  <h2 class="abs section-title" style="top:2052px">LATEST BLOGS</h2>
  <div class="abs arrow" style="left:33px;top:2298px"><svg width="18" height="18" viewBox="0 0 24 24" fill="none" stroke="#fff" stroke-width="2.5"><path d="m15 5-7 7 7 7"/></svg></div>
  <div class="abs arrow" style="left:1117px;top:2298px"><svg width="18" height="18" viewBox="0 0 24 24" fill="none" stroke="#fff" stroke-width="2.5"><path d="m9 5 7 7-7 7"/></svg></div>

  <article class="abs card" style="left:112px;top:2141px">
    <div class="card-img" role="img" aria-label="Business people shaking hands across a meeting table" style="background:linear-gradient(135deg,#c7ccd3,#7f8a97)"><span class="date">28TH MAY</span></div>
    <h4>AT VERO EOS ET ACCUSAMUS</h4>
    <p>Neque porro quisquam est, qui dolorem ipsum quia dolor sit amet,</p>
    <a>READ MORE</a>
  </article>
  <article class="abs card" style="left:442px;top:2141px">
    <div class="card-img" role="img" aria-label="Colleagues discussing work at a laptop" style="background:linear-gradient(135deg,#b7c4d2,#5e6d80)"><span class="date">20TH FEB</span></div>
    <h4>AT VERO EOS ET ACCUSAMUS</h4>
    <p>Neque porro quisquam est, qui dolorem ipsum quia dolor sit amet,</p>
    <a>READ MORE</a>
  </article>
  <article class="abs card" style="left:772px;top:2141px">
    <div class="card-img" role="img" aria-label="Smiling doctor holding a tablet" style="background:linear-gradient(135deg,#dfe3e8,#8b96a4)"><span class="date">2ND MAR</span></div>
    <h4>AT VERO EOS ET ACCUSAMUS</h4>
    <p>Neque porro quisquam est, qui dolorem ipsum quia dolor sit amet,</p>
    <a>READ MORE</a>
  </article>
</section>

<section class="abs testimonials">
  <h2 class="abs section-title" style="top:60px">CLIENT TESTIMONIALS</h2>
  <div class="abs" style="left:0;top:140px;width:1200px;text-align:center;font-size:20px;font-weight:600;color:var(--purple)">WHAT CLIENTS SAYS</div>
</section>
<p class="abs quote">Sed ut perspiciatis unde omnis iste natus error sit voluptatem accusantium doloremque laudantium, totam rem aperiam, eaque ipsa quae ab illo inventore veritatis et quasi architecto beatae vitae dicta sunt explicabo. Nemo enim ipsam voluptatem quia voluptas sit aspernatur aut odit aut fugit, sed quia consequuntur magni dolores eos qui ratione.</p>
<div class="abs avatar" role="img" aria-label="Client portrait"></div>
<div class="abs" style="left:580px;top:3044px">
  <div style="font-size:18px;font-weight:800;color:var(--purple)">LOREM IPSUM</div>
  <div style="font-size:15px;color:var(--ink);margin-top:10px">General Manager</div>
</div>
<div class="abs dots"><span></span><span></span><span></span></div>

<section>
  <div class="abs map" role="img" aria-label="City street map showing the office location"></div>
  <div class="abs" style="left:584px;top:3334px;width:504px;text-align:center;font-size:20px;font-weight:800;color:var(--purple)">SCHEDULE A 15 MINUTES CALL</div>
  <div class="abs field" style="left:584px;top:3392px;width:245px;height:45px">FIRST NAME<svg width="14" height="14" viewBox="0 0 24 24" fill="none" stroke="#333" stroke-width="2"><circle cx="12" cy="8" r="4"/><path d="M4 21a8 8 0 0 1 16 0z"/></svg></div>
  <div class="abs field" style="left:842px;top:3392px;width:246px;height:45px">LAST NAME<svg width="14" height="14" viewBox="0 0 24 24" fill="none" stroke="#333" stroke-width="2"><circle cx="12" cy="8" r="4"/><path d="M4 21a8 8 0 0 1 16 0z"/></svg></div>
  <div class="abs field" style="left:584px;top:3454px;width:245px;height:45px">MOBILE NUMBER<svg width="14" height="14" viewBox="0 0 24 24" fill="none" stroke="#333" stroke-width="2"><path d="M5 3h4l2 5-3 2a12 12 0 0 0 6 6l2-3 5 2v4a2 2 0 0 1-2 2A18 18 0 0 1 3 5a2 2 0 0 1 2-2z"/></svg></div>
  <div class="abs field" style="left:842px;top:3454px;width:246px;height:45px">EMAIL ADDRESS<svg width="16" height="14" viewBox="0 0 24 20" fill="none" stroke="#333" stroke-width="2"><rect x="2" y="2" width="20" height="16"/><path d="m2 2 10 9 10-9"/></svg></div>
  <div class="abs field" style="left:584px;top:3515px;width:504px;height:98px;align-items:flex-start;padding-top:16px">ENTER YOUR MESSAGE<svg width="16" height="14" viewBox="0 0 24 20" fill="none" stroke="#333" stroke-width="2"><rect x="2" y="2" width="20" height="13"/><path d="M6 15v4l4-4"/></svg></div>
  <span class="abs btn" style="left:584px;top:3644px;width:115px;height:41px;font-size:13px;border-radius:10px">SEND NOW</span>
</section>

<footer class="abs footer">
  <div class="abs brand" style="left:0;top:96px;width:1200px;justify-content:center">
    <span class="brand-dot"></span>
    <span class="brand-name" style="color:var(--yellow);font-size:24px;line-height:30px">MARROWIND WEALTH</span>
  </div>
  <nav class="abs footer-nav" style="left:292px;top:222px">
    <span>HOME</span><span>ABOUT US</span><span>OUR SERVICES</span><span>TESTIMONIALS</span><span>CONTACT US</span>
  </nav>
  <div class="abs social" style="left:539px;top:277px" aria-label="Social links">
    <span></span><span style="background:#e0306e"></span><span style="background:#e21b1b"></span>
  </div>
  <div class="abs" style="left:0;top:349px;width:1200px;text-align:center;font-size:13px;color:#fff">©2023 COPYRIGHTS. MARROWIND WEALTH. ALL RIGHTS RESERVED.</div>
</footer>

</body>
</html>
```